Copper Lantern

Need a business card for our restaurant. Restaurant and Bar in the mountains of North Idaho. Rustic looking card

rustic design, wood and metal looking, primarily neutral colors

• Name, address, phone number, website, email address

```html
<!DOCTYPE html>
<html lang="en">
<head>
<meta charset="utf-8">
<title>Copper Lantern – Business Card</title>
<link href="https://fonts.googleapis.com/css2?family=Montserrat:wght@400;500;700&display=swap" rel="stylesheet">
<style>
  :root {
    --backdrop: #2a2a2a;
    --card: #111111;
    --card-edge: #1c1c1c;
    --ink: #f2f2f2;
    --ink-soft: #d6d6d6;
    --silver-light: #cfcfcf;
    --silver-dark: #3a3a3a;
  }
  * { box-sizing: border-box; margin: 0; padding: 0; }
  html, body { width: 1200px; height: 874px; overflow: hidden; }
  body {
    background: var(--backdrop);
    font-family: "Montserrat", sans-serif;
    color: var(--ink);
    display: flex;
    flex-direction: column;
    align-items: center;
    justify-content: center;
    gap: 30px;
  }
  .card {
    position: relative;
    width: 700px;
    height: 400px;
    background: var(--card);
    border: 1px solid var(--card-edge);
    border-radius: 22px;
    overflow: hidden;
  }
  /* back side */
  .card-back { display: flex; align-items: center; justify-content: center; }
  .seal {
    width: 250px; height: 250px;
    border: 3px solid var(--silver-light);
    border-radius: 50%;
    display: flex; align-items: center; justify-content: center;
  }
  .seal-name {
    font-weight: 500; font-size: 24px; letter-spacing: 3px;
    color: var(--silver-light); text-transform: uppercase; text-align: center; line-height: 1.4;
  }
  /* front side */
  .brand {
    position: absolute; left: 56px; top: 42px;
    width: 130px; height: 130px;
    border: 2px solid var(--ink); border-radius: 50%;
    display: flex; align-items: center; justify-content: center;
  }
  .brand-name {
    font-weight: 500; font-size: 14px; letter-spacing: 2px;
    text-transform: uppercase; text-align: center; line-height: 1.4; color: var(--ink);
  }
  .address {
    position: absolute; left: 56px; top: 196px;
    font-size: 17px; line-height: 1.45; color: var(--ink-soft);
  }
  .contacts {
    position: absolute; left: 56px; top: 268px;
    list-style: none; font-size: 17px; line-height: 1.9; color: var(--ink-soft);
  }
  .contacts li { display: flex; align-items: center; gap: 10px; }
  .contacts svg { width: 14px; height: 14px; fill: var(--ink-soft); }
  .person {
    position: absolute; right: 40px; top: 150px;
    text-align: right; padding-right: 16px;
    border-right: 8px solid var(--ink);
  }
  .person-name { font-weight: 700; font-size: 25px; }
  .person-role { font-size: 15px; color: var(--ink-soft); margin-top: 2px; }
  .emblem-art {
    position: absolute; right: 80px; bottom: 0;
    width: 280px; height: 190px;
    border-radius: 40px 40px 0 0;
    background: linear-gradient(160deg, var(--silver-light), var(--silver-dark) 70%, var(--card));
    opacity: 0.85;
  }
</style>
</head>
<body>
  <section class="card card-back">
    <div class="seal">
      <p class="seal-name">Copper<br>Lantern</p>
    </div>
  </section>

  <section class="card card-front">
    <div class="brand"><p class="brand-name">Copper<br>Lantern</p></div>

    <p class="address">Your address, City<br>State, Zip 1234</p>

    <ul class="contacts">
      <li><svg viewBox="0 0 16 16"><path d="M3 1h3l1.5 4-2 1.3a9 9 0 0 0 4.2 4.2l1.3-2 4 1.5v3a1 1 0 0 1-1 1A13 13 0 0 1 2 2a1 1 0 0 1 1-1z"/></svg>123 456 789</li>
      <li><svg viewBox="0 0 16 16"><path d="M1 3h14v10H1z M1 3l7 6 7-6" fill="none" stroke="#d6d6d6" stroke-width="1.6"/></svg>info@yourmail.com</li>
      <li><svg viewBox="0 0 16 16"><circle cx="8" cy="8" r="6.5" fill="none" stroke="#d6d6d6" stroke-width="1.5"/><path d="M1.5 8h13M8 1.5c3 3.5 3 9.5 0 13M8 1.5c-3 3.5-3 9.5 0 13" fill="none" stroke="#d6d6d6" stroke-width="1.2"/></svg>www.yourwebsite.com</li>
    </ul>

    <div class="person">
      <p class="person-name">Calum Brenner</p>
      <p class="person-role">Managing Director</p>
    </div>

    <div class="emblem-art" role="img" aria-label="Large glossy silver emblem illustration of the restaurant mascot"></div>
  </section>
</body>
</html>
```